Brindle Recycling needs a new web design

We need a new web design for our company based in Austin, TX. We resell and recycling electronics such as laptops, computer components, Zelvotabs, Quorns, etc. Since our inception over ten years ago, we’ve become one of the premier electronics recycling and remarketing companies in Austin, Texas.

```html
<!DOCTYPE html>
<html lang="en">
<head>
<meta charset="utf-8">
<title>Brindle Recycling</title>
<link rel="stylesheet" href="https://fonts.googleapis.com/css2?family=Rubik:wght@400;500;700&family=Tinos:wght@400;700&display=swap">
<style>
:root{
  --blue:#1b6fc2;
  --blue-dark:#155a9e;
  --navy:#0f1e35;
  --green:#3ea53b;
  --green-dark:#1f5a23;
  --text:#4a4a4a;
  --heading:#1a1a1a;
  --grey-bg:#f2f3f5;
  --line:#e1e3e7;
  --white:#ffffff;
}
*{box-sizing:border-box;margin:0;padding:0}
html,body{width:1200px;height:3523px;overflow:hidden}
body{position:relative;font-family:"Rubik",Arial,sans-serif;color:var(--text);background:var(--white);font-size:12px;line-height:1.7}
.abs{position:absolute}
.serif{font-family:"Tinos","Times New Roman",serif}
.blue{color:var(--blue)}
.btn{position:absolute;display:flex;align-items:center;height:26px;padding:0 16px 0 4px;border-radius:13px;background:var(--blue);color:var(--white);font-size:11px;font-weight:500;gap:10px;white-space:nowrap}
.btn .dot{width:20px;height:20px;border-radius:50%;background:var(--white);display:flex;align-items:center;justify-content:center}
.btn .dot i{width:10px;height:10px;border:2px solid var(--blue);border-radius:2px}

/* top bar */
.topbar{top:0;left:0;width:1200px;height:24px;background:var(--blue)}
.social{display:flex;gap:6px;top:4px;left:216px}
.social span{width:16px;height:16px;background:var(--white);border-radius:2px}
.topbar .contact{right:210px;top:3px;color:var(--white);font-size:11px;display:flex;gap:20px}
/* header */
.header{top:24px;left:0;width:1200px;height:82px;background:var(--white)}
.brand{display:flex;align-items:center;gap:10px;left:211px;top:22px}
.brand .mark{width:36px;height:36px;border-radius:50%;border:3px solid var(--blue)}
.brand b{font-family:"Tinos",serif;font-size:19px;color:var(--navy);line-height:1;font-weight:700}
.nav{left:470px;top:31px;width:372px;display:flex;justify-content:space-between;font-size:11.5px;color:#333;white-space:nowrap}
.nav .active{color:var(--blue);border-bottom:2px solid var(--blue)}
.book{left:876px;top:28px;background:var(--navy);padding-right:22px}
.book .dot i{border-color:var(--navy)}

/* hero */
.hero{top:106px;left:0;width:1200px;height:516px;background:linear-gradient(180deg,#6ea9d9 0%,#a9d0ec 45%,#e6f2f8 62%,#7bbf3f 80%,#3f8f2a 100%);overflow:hidden}
.hero-curve{bottom:0;left:0;width:1200px;height:70px}
.hero h1{top:42px;width:1200px;text-align:center;font-size:30px;color:var(--heading);font-weight:700}
.hero p{top:92px;left:380px;width:440px;text-align:center;font-size:14px;color:#222;line-height:1.6}
.hero-art{left:280px;top:140px;width:640px;height:370px;border-radius:40px 40px 0 0;background:radial-gradient(ellipse at 50% 55%,#6fbf4d 0%,#9ea9a8 45%,rgba(180,190,195,0) 75%)}
.bubble{width:108px;height:108px;border-radius:50%;display:flex;align-items:center;justify-content:center;text-align:center;color:var(--white);font-size:12px;font-weight:500;line-height:1.3}
.b-light{background:var(--green)}
.b-dark{background:var(--green-dark)}

/* services */
.card-photo{height:206px}
.card-title{width:360px;height:72px;background:var(--white);text-align:center;padding-top:12px}
.card-title h2{font-size:22px;line-height:1.1;color:var(--heading)}
.card-title small{font-size:12px;color:#333}
.card-text{width:330px;text-align:center;font-size:11.5px;color:#555;line-height:1.75}

/* about */
.about{top:1186px;left:0;width:1200px;height:392px;background:linear-gradient(90deg,#ffffff 0%,#eef0f3 60%,#e9ebee 100%)}
.about-art{left:211px;top:46px;width:330px;height:306px;border-radius:50%;background:radial-gradient(circle,#7dc35a 0%,#4f9a3a 35%,#cfd5d9 62%,rgba(230,233,236,0) 72%)}
h2.sec{font-size:24px;font-weight:700;line-height:1.2}
.about .text{left:615px;width:390px;font-size:11.5px;line-height:1.75;color:#444}

/* computer recycling */
.video-frame{left:571px;top:1644px;width:415px;height:282px}
.video{left:587px;top:1663px;width:381px;height:239px;background:linear-gradient(135deg,#2c3a33 0%,#1a2320 60%,#0e1411 100%)}
.play{left:751px;top:1756px;width:54px;height:54px;border-radius:50%;border:2px solid rgba(255,255,255,.8);display:flex;align-items:center;justify-content:center}
.intro{left:211px;width:330px;font-size:11px;line-height:1.7}

/* certifications */
.certs{top:1992px;left:0;width:1200px;height:540px;background:var(--grey-bg)}
.cert-row{left:211px;width:400px;font-size:11px;color:#444;line-height:1.7;padding-bottom:12px;border-bottom:1px solid var(--line)}
.cert-row b{color:var(--blue);font-weight:500}
.badge{width:148px;height:140px;background:var(--white);display:flex;align-items:center;justify-content:center}
.badge span{width:78px;height:78px}

/* news */
.news-item{width:250px;display:flex;gap:10px}
.date{width:44px;flex:none;text-align:center}
.date .d{background:var(--navy);color:var(--white);font-size:24px;font-weight:700;line-height:40px}
.date .m{background:var(--blue);color:var(--white);font-size:9px;line-height:14px}
.news-item h3{font-size:13px;font-weight:500;color:#222;line-height:1.3}
.news-item p{font-size:10.5px;color:#555;line-height:1.6;margin-top:6px}
.news-item a{font-size:10.5px;color:var(--blue);text-decoration:underline}

/* map & contact */
.map{top:2825px;left:0;width:1200px;height:404px;background:linear-gradient(160deg,#e8ecef 0%,#dfe6e2 40%,#e6e9ec 100%)}
.band{top:3229px;left:0;width:1200px;height:294px;background:var(--blue)}
.contact-form{left:211px;top:3022px;width:392px;height:418px;background:var(--white);padding:28px 27px}
.contact-form h2{text-align:center}
.contact-form p{font-size:11px;text-align:center;color:#555;line-height:1.6;margin:10px 0 14px}
.fields{display:grid;grid-template-columns:1fr 1fr;gap:8px}
.field{height:32px;border:1px solid #dcdfe3;background:#f6f7f9;font-size:10.5px;color:#999;padding:0 10px;line-height:30px}
.field.full{grid-column:1 / 3}
.field.first{border-color:var(--blue);background:var(--white);color:#888}
.field.msg{height:84px}
.send{margin-top:10px;height:32px;background:var(--blue);color:var(--white);text-align:center;line-height:32px;font-size:11px;font-weight:500}
.contact-card{left:603px;top:3022px;width:386px;height:418px;background:var(--navy);padding:14px}
.contact-card .inner{width:100%;height:100%;border:1px solid rgba(255,255,255,.6);text-align:center;color:var(--white);padding-top:50px}
.contact-card .logo{display:flex;align-items:center;justify-content:center;gap:10px;margin-bottom:30px}
.contact-card .logo .mark{width:44px;height:44px;border-radius:50%;border:3px solid var(--white)}
.contact-card .logo b{font-family:"Tinos",serif;font-size:24px;font-weight:700;line-height:1}
.contact-card .lbl{font-size:10px;color:var(--blue);letter-spacing:1px;margin-top:12px}
.contact-card .val{font-size:14px;line-height:1.5}
.card-social{display:flex;justify-content:center;gap:8px;margin-top:20px}
.card-social span{width:18px;height:18px;background:var(--white);border-radius:2px}
.footer-note{top:3472px;width:1200px;text-align:center;font-size:10.5px;color:var(--white)}
</style>
</head>
<body>

<div class="abs topbar">
  <div class="abs social"><span></span><span></span><span></span></div>
  <div class="abs contact"><span>&#9742; (512) 555-0147</span><span>&#9993; hello@brindlerecycling.com</span></div>
</div>

<header class="abs header">
  <div class="abs brand"><span class="mark"></span><b>Brindle<br><span style="font-size:12px;font-weight:400">Recycling</span></b></div>
  <nav class="abs nav"><span class="active">Home</span><span>About</span><span>Services</span><span>Certifications</span><span>News</span><span>Contact</span></nav>
  <div class="btn book"><span class="dot"><i></i></span>Book Online</div>
</header>

<section class="abs hero">
  <h1 class="abs serif"><span class="blue">Recycling Today</span> Reuse Tomorrow</h1>
  <p class="abs">We resell and recycling electronics such as laptops, computer components, Zelvotabs, Quorns, etc.</p>
  <div class="abs hero-art" role="img" aria-label="Recycling bin overflowing with laptops, keyboards and old computer parts"></div>
  <div class="abs bubble b-dark" style="left:263px;top:244px">Other<br>Components</div>
  <div class="abs bubble b-light" style="left:364px;top:192px">Laptops</div>
  <div class="abs bubble b-light" style="left:364px;top:310px">Zelvotabs</div>
  <div class="abs bubble b-light" style="left:716px;top:188px">Computers</div>
  <div class="abs bubble b-dark" style="left:820px;top:247px">Small<br>Devices</div>
  <div class="abs bubble b-light" style="left:716px;top:305px">Quorns</div>
  <svg class="abs hero-curve" viewBox="0 0 1200 70" preserveAspectRatio="none"><path d="M0 0 Q600 110 1200 0 L1200 70 L0 70 Z" fill="#fff"/></svg>
</section>

<div class="abs card-photo" style="left:211px;top:662px;width:383px;background:linear-gradient(180deg,#5d8fc9,#a7c3e0 55%,#2d5fa3)" role="img" aria-label="Blue recycling bin filled with old monitors and keyboards under a blue sky"></div>
<div class="abs card-title" style="left:222px;top:868px"><h2 class="serif"><span class="blue">Electronic</span> Recycling</h2><small>Environmentally Friendly</small></div>
<p class="abs card-text" style="left:237px;top:950px">At Brindle Recycling, we strive to keep the environment clean through our wide range of services. Our E-Waste Recycling services were designed to simplify the recycling process for residents in the Austin area. Contact us today and see how you can contribute to making this world a cleaner place.</p>
<div class="btn" style="left:330px;top:1084px"><span class="dot"><i></i></span>Schedule A Pickup</div>

<div class="abs card-photo" style="left:611px;top:662px;width:380px;background:linear-gradient(180deg,#c9c2b4,#8e8a82 55%,#5d5a55)" role="img" aria-label="Recycling crew loading a pickup of old electronics beside parked cars"></div>
<div class="abs card-title" style="left:621px;top:868px"><h2 class="serif">Recycling <span class="blue">Pickup</span></h2><small>We Come To You</small></div>
<p class="abs card-text" style="left:636px;top:950px">At Brindle Recycling, we go out of our way to make sure your recycling process is made easy as possible. Our Recycling Pickup service is designed to simplify all of your recycling needs. Take a look at all the services we offer and get in touch to see how you can start the process today!</p>
<div class="btn" style="left:724px;top:1084px"><span class="dot"><i></i></span>Schedule A Pickup</div>

<section class="abs about">
  <div class="abs about-art" role="img" aria-label="Green recycling arrows circling a bin of electronics"></div>
  <h2 class="abs sec serif" style="left:615px;top:76px"><span class="blue">About</span> Brindle Recycling</h2>
  <p class="abs text" style="top:118px;color:var(--blue-dark)">At Brindle Recycling, we're committed to providing environmentally friendly recycling solutions to Austin and the surrounding areas.</p>
  <p class="abs text" style="top:170px">Founded in 2006, our mission is to process your materials in a safe, non-hazardous manner — with an aim to keep the world environmentally clean. As a certified recycling center, we believe in promoting smart recycling habits in order to achieve long lasting results.</p>
  <div class="btn" style="left:613px;top:300px"><span class="dot"><i></i></span>Schedule A Pickup</div>
</section>

<h2 class="abs sec serif" style="left:211px;top:1636px"><span class="blue">Computer Recycling</span><br>Made Easy</h2>
<p class="abs intro" style="top:1714px">Want to make a difference to our environment and planet? Brindle Recycling is here to help! Brindle Recycling has been helping keep the environment healthy since 2006.</p>
<p class="abs intro" style="top:1786px">we specialize in recycling services that help citizens become experts at reducing waste. We have a passion to keep our world clean and are here to guide you through all the stages of the recycling process.</p>
<div class="btn" style="left:211px;top:1880px"><span class="dot"><i></i></span>Read More</div>
<svg class="abs video-frame" viewBox="0 0 415 282"><path d="M0 120 V0 H160" fill="none" stroke="#1b6fc2" stroke-width="14"/><path d="M415 162 V282 H255" fill="none" stroke="#1b6fc2" stroke-width="14"/></svg>
<div class="abs video" role="img" aria-label="Video still of a hand selecting a recycle symbol on a dark screen"></div>
<div class="abs play"><svg width="20" height="22" viewBox="0 0 20 22"><path d="M3 2 L18 11 L3 20 Z" fill="#fff"/></svg></div>

<section class="abs certs">
  <h2 class="abs sec serif" style="top:56px;width:1200px;text-align:center"><span class="blue">Certified</span> Recyclers</h2>
  <p class="abs" style="left:340px;top:100px;width:520px;text-align:center;font-size:11px;line-height:1.7">Processing of electronic assets and electronic scrap, all associated site operations and maintenance, as well as the supporting financial and administrative functions related to these activities and operations.</p>
  <p class="abs cert-row" style="top:178px">Has been assessed by Meridian Registrar and found to be in compliance with the following <b>Environmental Management</b> Standard: <b>ISO 14001:2015</b></p>
  <p class="abs cert-row" style="top:260px">Has been assessed by Meridian Registrar and found to be in compliance with the following <b>Occupational Health and Safety</b> Standard: <b>OHSAS 18001:2007</b></p>
  <p class="abs cert-row" style="top:330px">Has been assessed by Meridian Registrar and found to be in Compliance with the following <b>Responsible Recycling</b> Standard: <b>RR:2013</b></p>
  <p class="abs" style="left:211px;top:390px;font-size:11px">State Environmental Quality Board : <b class="blue" style="font-weight:500">REG-7741</b></p>
  <div class="btn" style="left:211px;top:440px"><span class="dot"><i></i></span>View Full Certifications</div>
  <div class="abs badge" style="left:676px;top:180px"><span style="background:#d0dbe8;border-radius:8px"></span></div>
  <div class="abs badge" style="left:843px;top:180px"><span style="border:3px solid #888;border-radius:50%"></span></div>
  <div class="abs badge" style="left:676px;top:333px"><span style="background:#2f4f9c;border-radius:50%"></span></div>
  <div class="abs badge" style="left:843px;top:333px"><span style="border:4px solid var(--green);border-radius:50%"></span></div>
</section>

<h2 class="abs sec serif" style="left:211px;top:2586px"><span class="blue">Brindle</span> News</h2>
<svg class="abs" style="left:966px;top:2594px" width="24" height="14" viewBox="0 0 24 14"><path d="M7 2 L2 7 L7 12" fill="none" stroke="#0f1e35" stroke-width="2"/><path d="M17 2 L22 7 L17 12" fill="none" stroke="#1b6fc2" stroke-width="2"/></svg>
<div class="abs news-item" style="left:211px;top:2654px"><div class="date"><div class="d">20</div><div class="m">JUN'18</div></div><div><h3>Proin condimentum mentum</h3><p>Nullam ac urna eu felis dapibus condimentum sit amet a augue. Sed non neque elit.</p><a>Readmore</a></div></div>
<div class="abs news-item" style="left:477px;top:2654px"><div class="date"><div class="d">20</div><div class="m">JUN'18</div></div><div><h3>Proin condimentum mentum</h3><p>Nullam ac urna eu felis dapibus condimentum sit amet a augue. Sed non neque elit.</p><a>Readmore</a></div></div>
<div class="abs news-item" style="left:742px;top:2654px"><div class="date"><div class="d">20</div><div class="m">JUN'18</div></div><div><h3>Proin condimentum mentum</h3><p>Nullam ac urna eu felis dapibus condimentum sit amet a augue. Sed non neque elit.</p><a>Readmore</a></div></div>

<div class="abs map" role="img" aria-label="Street map of the north Austin area around the recycling center"></div>
<svg class="abs" style="left:544px;top:2932px" width="20" height="28" viewBox="0 0 20 28"><path d="M10 27 C10 27 1 15 1 10 A9 9 0 0 1 19 10 C19 15 10 27 10 27 Z" fill="#e53935"/><circle cx="10" cy="10" r="3.5" fill="#8b1c1c"/></svg>
<div class="abs band"></div>
<div class="abs contact-form">
  <h2 class="sec serif blue">Contact Us</h2>
  <p>Interested in helping to make the world a greener place? Get in touch with Brindle Recycling, and learn more about the wide range of recycling services and facilities that are at your disposal.</p>
  <div class="fields">
    <div class="field first">Name</div><div class="field">Email</div>
    <div class="field">Phone</div><div class="field">Subject</div>
    <div class="field full">Address</div>
    <div class="field full msg">Message</div>
  </div>
  <div class="send">SEND MESSAGE</div>
</div>
<div class="abs contact-card">
  <div class="inner">
    <div class="logo"><span class="mark"></span><b>Brindle<br><span style="font-size:15px;font-weight:400">Recycling</span></b></div>
    <div class="lbl">ADDRESS</div>
    <div class="val">4120 Cedar Hollow Rd<br>Austin TX USA 78700</div>
    <div class="lbl">PHONE</div>
    <div class="val">(512) 555-0147</div>
    <div class="lbl">EMAIL</div>
    <div class="val">hello@brindlerecycling.com</div>
    <div class="card-social"><span></span><span></span><span></span></div>
  </div>
</div>
<p class="abs footer-note">©2018 by Brindle Recycling. All Rights Reserved</p>

</body>
</html>
```